Tall Fern Roofing Business Card

Need a business card with the logo that was designed here

Contact Information for Business Card

Name, Title, Phone, Email, Website, Company name

```html
<!DOCTYPE html>
<html lang="en">
<head>
<meta charset="utf-8">
<title>Tall Fern Roofing – Business Card</title>
<link rel="stylesheet" href="https://fonts.googleapis.com/css2?family=Montserrat:wght@400;600;700&display=swap">
<style>
  :root {
    --page-bg: #e9e6e1;
    --card-bg: #f6f5f3;
    --card-edge: #d8d5d0;
    --brand-blue: #2f63b5;
    --bar-blue: #2d5a9c;
    --text-grey: #555659;
  }
  html, body {
    margin: 0;
    padding: 0;
    width: 1200px;
    height: 897px;
    overflow: hidden;
    background: var(--page-bg);
    font-family: "Montserrat", sans-serif;
  }
  .card {
    position: absolute;
    left: 80px;
    top: 163px;
    width: 1040px;
    height: 570px;
    border-radius: 26px;
    background: linear-gradient(135deg, #fafafa 0%, var(--card-bg) 55%, #eeece8 100%);
    border: 1px solid var(--card-edge);
    box-shadow: 0 12px 40px rgba(0, 0, 0, 0.08);
    overflow: hidden;
  }
  .brand {
    position: absolute;
    left: 52px;
    top: 100px;
    display: flex;
    align-items: center;
    gap: 12px;
    color: var(--brand-blue);
    font-weight: 700;
    font-size: 34px;
    letter-spacing: 0.5px;
  }
  .brand-square {
    width: 22px;
    height: 22px;
    background: var(--brand-blue);
  }
  .accent-bar {
    position: absolute;
    left: 0;
    top: 232px;
    width: 23px;
    height: 61px;
    background: var(--bar-blue);
  }
  .person-name {
    position: absolute;
    left: 52px;
    top: 228px;
    margin: 0;
    color: var(--brand-blue);
    font-weight: 700;
    font-size: 33px;
    letter-spacing: 1px;
  }
  .person-title {
    position: absolute;
    left: 52px;
    top: 270px;
    margin: 0;
    color: var(--text-grey);
    font-size: 21px;
    letter-spacing: 0.8px;
  }
  .address {
    position: absolute;
    left: 52px;
    top: 322px;
    margin: 0;
    color: var(--text-grey);
    font-size: 21px;
    line-height: 33px;
    font-style: normal;
    letter-spacing: 0.8px;
  }
  .contact-list {
    position: absolute;
    left: 52px;
    top: 410px;
    margin: 0;
    padding: 0;
    list-style: none;
    color: var(--text-grey);
    font-size: 21px;
    letter-spacing: 0.8px;
  }
  .contact-list li {
    display: flex;
    align-items: center;
    gap: 10px;
    height: 39px;
  }
  .contact-icon {
    width: 18px;
    height: 18px;
    fill: var(--text-grey);
    flex: none;
  }
</style>
</head>
<body>
  <section class="card">
    <div class="brand">
      <span class="brand-square"></span>
      <span class="brand-name">Tall Fern Roofing</span>
    </div>

    <div class="accent-bar"></div>
    <h1 class="person-name">DECLAN HARWOOD</h1>
    <p class="person-title">Managing Director</p>

    <address class="address">1480 W Harbor Street<br>Marlow County Name 4172</address>

    <ul class="contact-list">
      <li>
        <svg class="contact-icon" viewBox="0 0 24 24" aria-hidden="true"><path d="M6.6 10.8a15.1 15.1 0 0 0 6.6 6.6l2.2-2.2a1 1 0 0 1 1-.25 11.4 11.4 0 0 0 3.6.57 1 1 0 0 1 1 1V20a1 1 0 0 1-1 1A17 17 0 0 1 3 4a1 1 0 0 1 1-1h3.5a1 1 0 0 1 1 1 11.4 11.4 0 0 0 .57 3.6 1 1 0 0 1-.25 1z"/></svg>
        <span>0470 518 362</span>
      </li>
      <li>
        <svg class="contact-icon" viewBox="0 0 24 24" aria-hidden="true"><path d="M2 6a2 2 0 0 1 2-2h16a2 2 0 0 1 2 2v12a2 2 0 0 1-2 2H4a2 2 0 0 1-2-2zm2 .4V8l8 5 8-5V6.4l-8 5z"/></svg>
        <span>info@tallfernroofing.com</span>
      </li>
      <li>
        <svg class="contact-icon" viewBox="0 0 24 24" aria-hidden="true"><path d="M12 2a10 10 0 1 0 0 20 10 10 0 0 0 0-20zm6.9 6h-2.9a15.7 15.7 0 0 0-1.4-3.6A8 8 0 0 1 18.9 8zM12 4a13.8 13.8 0 0 1 1.9 4h-3.8A13.8 13.8 0 0 1 12 4zM4.3 14a8 8 0 0 1 0-4h3.4a16.5 16.5 0 0 0 0 4zm.8 2h2.9a15.7 15.7 0 0 0 1.4 3.6A8 8 0 0 1 5.1 16zM8 8H5.1a8 8 0 0 1 4.3-3.6A15.7 15.7 0 0 0 8 8zm4 12a13.8 13.8 0 0 1-1.9-4h3.8A13.8 13.8 0 0 1 12 20zm2.3-6H9.7a14.7 14.7 0 0 1 0-4h4.6a14.7 14.7 0 0 1 0 4zm.3 5.6a15.7 15.7 0 0 0 1.4-3.6h2.9a8 8 0 0 1-4.3 3.6zm1.7-5.6a16.5 16.5 0 0 0 0-4h3.4a8 8 0 0 1 0 4z"/></svg>
        <span>www.tallfernroofing.com</span>
      </li>
    </ul>
  </section>
</body>
</html>
```